Dental Practice Billboard Design

We are a newer dental practice in need of a simple but appealing billboard for our growing dental practice to attract new patients. The practice is owned by husband and wife dentists and is family friendly in a small town in Kentucky. We try to be very friendly and caring to our patients. Would prefer a blue background for the billboard and our tooth logo to be prominent. We are partial to the Patua One font used in the image below but please feel free to tweak it as you deem necessary. The shape of the uppercase D and lowercase g are why we like that font, so fonts with a similarly shaped “D” and “g” would work as well. Please include our phone number (555) 847-1390. Please see our website Harlowbrookdentistry.example for more info on the practice if needed. Thank you! Looking forward to seeing your creation.
Updates

The dimensions will be 12ft x 24ft (3.6576m x 7.3152m). Apologies for not including this in the original prompt. Thank you all for your submissions.

Industry/Entity Type

Dental

Font styles to use
Other font styles liked:
• Patua One

Colors
0054AA
0677BA
7BADD7
CADEEF
E8F1F8
0094D4
00A9DD
6FCCEA
C7EBF8
E9F6FB
00AB8E
00BBA5
67D7C9
C6EFE9
E9F9F6
59FF00
82FF00
B8FF75
E3FFCB
F4FFEA

Requirements
Must have
• Phone number, website, Logo, Practice name “Harlow Brook Dentistry”
Should not have
• A tagline or slogan

```html
<!DOCTYPE html>
<html lang="en">
<head>
<meta charset="utf-8">
<title>Harlow Brook Dentistry — Billboard</title>
<link href="https://fonts.googleapis.com/css2?family=Patua+One&display=swap" rel="stylesheet">
<style>
  :root {
    --navy: #012158;
    --green: #0ab00a;
    --white: #ffffff;
    --backdrop: #e9edf2;
  }
  * { margin: 0; padding: 0; box-sizing: border-box; }
  html, body {
    width: 1200px;
    height: 722px;
    overflow: hidden;
    background: var(--backdrop);
  }
  .billboard {
    position: absolute;
    left: 40px;
    top: 81px;
    width: 1120px;
    height: 560px;
    background: var(--navy);
    font-family: "Patua One", Georgia, serif;
    color: var(--white);
    overflow: hidden;
  }
  .brand {
    position: absolute;
    top: 0;
    left: 0;
    width: 100%;
    height: 300px;
    display: flex;
    align-items: center;
    justify-content: center;
    gap: 34px;
  }
  .brand-mark {
    width: 150px;
    height: 150px;
    border-radius: 50%;
    background: var(--green);
    flex: none;
  }
  .brand-name {
    display: flex;
    flex-direction: column;
    line-height: 1;
    font-weight: 400;
    color: var(--white);
  }
  .brand-name .primary { font-size: 100px; }
  .brand-name .secondary { font-size: 58px; margin-top: 10px; padding-left: 4px; }
  .accent-band {
    position: absolute;
    top: 300px;
    left: 0;
    width: 100%;
    height: 104px;
    background: var(--green);
  }
  .contact-row {
    position: absolute;
    top: 404px;
    left: 0;
    width: 100%;
    height: 156px;
    display: flex;
    align-items: center;
    justify-content: center;
    gap: 28px;
  }
  .contact-item {
    display: flex;
    align-items: center;
    gap: 14px;
  }
  .contact-icon {
    width: 58px;
    height: 58px;
    border-radius: 50%;
    background: var(--green);
    display: flex;
    align-items: center;
    justify-content: center;
    flex: none;
  }
  .contact-icon svg { width: 32px; height: 32px; }
  .phone { font-size: 62px; line-height: 1; letter-spacing: -1px; }
  .website { font-size: 34px; line-height: 1; }
</style>
</head>
<body>
  <section class="billboard">
    <header class="brand">
      <span class="brand-mark" aria-hidden="true"></span>
      <h1 class="brand-name">
        <span class="primary">Harlow Brook</span>
        <span class="secondary">Dentistry</span>
      </h1>
    </header>

    <div class="accent-band" aria-hidden="true"></div>

    <footer class="contact-row">
      <div class="contact-item">
        <span class="contact-icon" aria-hidden="true">
          <svg viewBox="0 0 24 24"><path fill="#fff" d="M6.6 10.8a15.1 15.1 0 0 0 6.6 6.6l2.2-2.2a1 1 0 0 1 1-.25 11.4 11.4 0 0 0 3.6.57 1 1 0 0 1 1 1V20a1 1 0 0 1-1 1A17 17 0 0 1 3 4a1 1 0 0 1 1-1h3.5a1 1 0 0 1 1 1c0 1.25.2 2.450.57 3.57a1 1 0 0 1-.25 1z"/></svg>
        </span>
        <span class="phone">(555) 847-1390</span>
      </div>
      <div class="contact-item">
        <span class="contact-icon" aria-hidden="true">
          <svg viewBox="0 0 24 24"><rect x="4" y="5" width="16" height="11" rx="1" fill="none" stroke="#fff" stroke-width="2"/><rect x="2" y="17.5" width="20" height="2.5" rx="1" fill="#fff"/></svg>
        </span>
        <span class="website">Harlowbrookdentistry.example</span>
      </div>
    </footer>
  </section>
</body>
</html>
```